Job Recruiting Agemcy

almost like my current site www.plorvex.com but with these changes see and what i meant about the across the to the site says home job companies categories pages blog and login sign up that should only be the 4 i said only 1 home 2 industries 3 jobs 4 contact us. and remove latest blog post and our partners because that's not us we have to post acuarte information thanks and the name of the company if your using is is work and careful hiring partners and want it easy for us to post and remove jobs and where it emails us every resume or person that applies

Requirements
Must have
• must send email to us when an application is submitted and try to incorparate the colors of current site
Nice to have
• i want a pretty basic site for now just like the one i have but with all thats above were its easy for me being the own to be able to post jobs and everything

```html
<!DOCTYPE html>
<html lang="en">
<head>
<meta charset="utf-8">
<title>Plorvex — Work and Careful Hiring Partners</title>
<link href="https://fonts.googleapis.com/css2?family=Rajdhani:wght@400;500;600;700&family=Roboto:wght@400;500&display=swap" rel="stylesheet">
<style>
:root{
  --green:#2f6a45;
  --green-dark:#24553a;
  --red:#e2434f;
  --purple:#7a1fa6;
  --ink:#333;
  --muted:#666;
  --band:#f3f3f3;
  --line:#e2e2e2;
  --white:#fff;
}
*{box-sizing:border-box;margin:0;padding:0}
html,body{width:1200px;height:3836px;overflow:hidden}
body{position:relative;font-family:'Rajdhani',sans-serif;color:var(--ink);background:#fff}
.abs{position:absolute}
.red{color:var(--red)}

/* header */
.site-header{position:absolute;left:0;top:0;width:1200px;height:109px;background:var(--green);z-index:3}
.brand-disc{position:absolute;left:111px;top:38px;width:178px;height:178px;border-radius:50%;background:var(--green);z-index:4;display:flex;flex-direction:column;align-items:center;justify-content:center;color:var(--white)}
.brand-disc .name{font-weight:700;font-size:30px;letter-spacing:1px;color:var(--white)}
.brand-disc .tag{font-size:10px;font-weight:600;letter-spacing:.5px;color:var(--white);margin-top:2px}
.nav{position:absolute;top:0;left:0;height:109px;width:1200px;z-index:5}
.nav a{position:absolute;top:43px;font-size:15px;font-weight:600;color:var(--white);text-decoration:none;letter-spacing:.3px}
.nav .pill{top:33px;height:40px;border:1.5px solid var(--white);border-radius:20px;display:flex;align-items:center;justify-content:center}

/* hero */
.hero{position:absolute;left:0;top:109px;width:1200px;height:674px;background:linear-gradient(180deg,#ecebe8 0%,#dcdbd8 45%,#9b9996 75%,#5d5b58 100%)}
.hero-kicker{position:absolute;top:238px;width:1200px;text-align:center;font-size:24px;font-weight:600;color:#333}
.hero-title{position:absolute;top:276px;width:1200px;text-align:center;font-size:58px;font-weight:700;color:var(--green);letter-spacing:1px}
.field{position:absolute;top:357px;height:49px;background:#fff;border:1px solid #d6d6d6;font-size:18px;color:#555;padding:12px 14px;font-weight:500}
.search-btn{position:absolute;left:881px;top:357px;width:121px;height:49px;background:var(--red);color:#fff;font-size:17px;font-weight:600;display:flex;align-items:center;justify-content:center}

/* welcome */
.section-title{position:absolute;width:1200px;text-align:center;font-size:36px;font-weight:600;color:var(--green);letter-spacing:.5px}
.welcome-copy{position:absolute;top:903px;left:300px;width:600px;text-align:center;font-size:15px;line-height:30px;color:#444;font-weight:500}
.feature{position:absolute;top:1038px;width:230px;height:226px;border:1.5px solid #ddd;border-radius:4px;text-align:center}
.feature .icon{width:72px;height:72px;margin:30px auto 0;border-radius:10px;background:linear-gradient(135deg,#e9f1ec,#f7e3e5)}
.feature h3{margin-top:20px;font-size:15px;font-weight:700;color:#222}
.feature p{margin-top:10px;font-size:13.5px;line-height:23px;color:#666;font-weight:500;padding:0 22px}

/* about */
.about-band{position:absolute;left:0;top:1420px;width:1200px;height:480px;background:var(--band)}
.about-frame{position:absolute;left:132px;top:1374px;width:414px;height:469px;border:4px solid var(--green);border-radius:4px}
.about-photo{position:absolute;left:121px;top:1356px;width:415px;height:472px;background:linear-gradient(135deg,#dfe3e4,#9aa3a8 55%,#3e4a5a)}
.about-title{position:absolute;left:582px;top:1480px;font-size:36px;font-weight:600;color:var(--green)}
.about-copy{position:absolute;left:582px;top:1552px;width:508px;font-size:14.5px;line-height:30px;color:#555;font-weight:500;text-align:justify}
.btn{position:absolute;display:flex;align-items:center;justify-content:center;color:#fff;font-weight:600;font-size:17px;border-radius:30px}

/* seeking */
.seek{position:absolute;left:0;top:1900px;width:1200px;height:532px;background:radial-gradient(ellipse at 55% 45%,#4a4642 0%,#2e2c2a 55%,#1b1a19 100%)}
.seek-title{position:absolute;top:2064px;width:1200px;text-align:center;font-size:48px;font-weight:600;color:#fff;letter-spacing:1px}
.seek-sub{position:absolute;top:2136px;width:1200px;text-align:center;font-size:20px;font-weight:500;color:#fff;letter-spacing:.5px}

/* jobs */
.jobs-sub{position:absolute;top:2546px;width:1200px;text-align:center;font-size:16px;color:#555;font-weight:500}
.jobs-table{position:absolute;left:155px;top:2623px;width:893px;height:352px;background:#fff;border-radius:6px;box-shadow:0 0 10px rgba(0,0,0,.08)}
.job-row{position:absolute;left:0;width:893px;border-bottom:1px solid #eee}
.job-row .badge{position:absolute;left:13px;width:109px;height:58px;border:1.5px solid #e6e6e6;border-radius:4px;display:flex;align-items:center;justify-content:center}
.job-row .badge i{width:52px;height:18px;border-radius:9px;background:#cfd6dc}
.job-row .role{position:absolute;left:140px;font-family:'Roboto',sans-serif;font-size:12px;font-weight:500;color:#222;letter-spacing:.3px}
.job-row .role em{display:block;font-size:11px;color:#888;font-weight:400;margin-top:2px}
.job-row .sep{position:absolute;top:0;bottom:0;width:1px;background:#eee}
.job-row .loc{position:absolute;left:351px;font-size:15px;color:#666;font-weight:500;display:flex;align-items:center;gap:8px}
.job-row .type{position:absolute;left:551px;width:143px;height:38px;border-radius:20px;color:#fff;font-size:14px;font-weight:700;display:flex;align-items:center;justify-content:center}
.job-row .price{position:absolute;left:783px;font-size:19px;font-weight:600;color:var(--red)}

/* testimonial */
.portrait{position:absolute;left:174px;top:3113px;width:260px;height:260px;border-radius:50%;background:linear-gradient(160deg,#6f8a93,#4c6670 60%,#2a3238)}
.quote-dot{position:absolute;left:276px;top:3346px;width:56px;height:56px;border-radius:50%;background:var(--red);color:#fff;font-size:40px;font-weight:700;display:flex;align-items:center;justify-content:center;line-height:1}
.test-title{position:absolute;left:485px;top:3118px;font-size:36px;font-weight:600;color:var(--green)}
.test-copy{position:absolute;left:489px;top:3190px;width:580px;font-family:'Roboto',sans-serif;font-size:12.5px;line-height:27px;color:#555}
.test-name{position:absolute;left:489px;top:3318px;font-size:21px;color:var(--green);font-weight:500}
.test-name small{font-size:12px;color:#555}

/* footer */
.footer{position:absolute;left:0;top:3446px;width:1200px;height:390px;background:var(--green)}
.on-footer{color:var(--white)}
.foot-brand{position:absolute;left:150px;top:3680px;width:210px;text-align:center}
.foot-brand .name{font-size:38px;font-weight:700;letter-spacing:1px}
.foot-brand .tag{font-size:12px;font-weight:600;margin-top:4px}
.foot-h{position:absolute;top:3502px;font-size:20px;font-weight:500;letter-spacing:.5px}
.foot-links{position:absolute;left:420px;top:3552px;list-style:none;font-family:'Roboto',sans-serif;font-size:12px}
.foot-links li{height:30px;display:flex;gap:16px}
.foot-contact{position:absolute;left:618px;top:3552px;font-family:'Roboto',sans-serif;font-size:12.5px;line-height:29.5px}
.news-copy{position:absolute;left:862px;top:3552px;width:230px;font-family:'Roboto',sans-serif;font-size:11.5px;line-height:28px}
.news-input{position:absolute;left:862px;top:3618px;width:226px;height:40px;background:#fff;color:#555;font-family:'Roboto',sans-serif;font-size:11px;padding:13px 14px}
.news-btn{position:absolute;left:862px;top:3670px;width:98px;height:36px;background:var(--red);color:#fff;font-family:'Roboto',sans-serif;font-size:13px;display:flex;align-items:center;justify-content:center}
.copyright{position:absolute;left:112px;top:3788px;font-family:'Roboto',sans-serif;font-size:14px}
.social{position:absolute;top:3780px;width:36px;height:36px;border:1.5px solid var(--white);border-radius:50%}
.foot-code{position:absolute;left:1102px;top:3791px;font-family:'Roboto',sans-serif;font-size:13px}
</style>
</head>
<body>

<header class="site-header"></header>
<div class="brand-disc"><span class="name" style="margin-top:40px">PLORVEX</span><span class="tag">SERVICING YOU SINCE 1980</span></div>
<nav class="nav">
  <a style="left:511px">HOME</a>
  <a style="left:595px">INDUSTRIES</a>
  <a style="left:719px">JOBS</a>
  <a style="left:801px">CONTACT US</a>
  <a class="pill" style="left:893px;width:94px">LOGIN</a>
  <a class="pill" style="left:994px;width:95px">SIGNUP</a>
</nav>

<section class="hero" role="img" aria-label="Six smiling job candidates in business clothes seated against a white brick wall"></section>
<div class="hero-kicker">SEARCH FROM 21 JOB OFFERS</div>
<h1 class="hero-title">YOUR CAREER STARTS HERE!</h1>
<div class="field" style="left:198px;width:335px">Keywords</div>
<div class="field" style="left:540px;width:336px">Location</div>
<div class="search-btn">SEARCH</div>

<h2 class="section-title" style="top:840px">WELCOME TO <span class="red">PLORVEX</span></h2>
<p class="welcome-copy">We have over 35 years of Specialized Recruiting and souring experience. We cover a broad spectrum of industries to include some of the top aerospace and pharmaceutical commercial companies of today.</p>

<div class="feature" style="left:112px"><div class="icon" role="img" aria-label="Job manager icon"></div><h3>EASY JOB MANAGER</h3><p>Nulla at rutrum ipsum. Praese augue quam, facilisis</p></div>
<div class="feature" style="left:360px"><div class="icon" role="img" aria-label="Admin search icon"></div><h3>A FAMILIAR ADMIN UI</h3><p>Nulla at rutrum ipsum. Praese augue quam, facilisis</p></div>
<div class="feature" style="left:608px"><div class="icon" role="img" aria-label="Job listings icon"></div><h3>FILTERABLE JOB LISTINGS</h3><p>Nulla at rutrum ipsum. Praese augue quam, facilisis</p></div>
<div class="feature" style="left:857px"><div class="icon" role="img" aria-label="Job submission icon"></div><h3>FRONTED JOB SUBMISSION</h3><p>Nulla at rutrum ipsum. Praese augue quam, facilisis</p></div>

<section class="about-band"></section>
<div class="about-frame"></div>
<div class="about-photo" role="img" aria-label="Two colleagues at a white desk reviewing work on a laptop"></div>
<h2 class="about-title">ABOUT <span class="red">US</span></h2>
<p class="about-copy">Maecenas mollis dictum lectus quis scelerisque. Nulla at rutrum ipsum. Praesent augue quam, facilisis vitae felis vel, convallis convallis nisi. Donec maximus accu msan purus vel tempus. Aenean pretium luctus velit id fermentum. Aenean non velit non nulla interdum venenatis. Nunc et massa leo. Vestibulum a pretium dolor. Proin et fermentum sapien. Cras malesuada neque ac purus fermentum, a placerat quam malesuada. Quisque sollicitudin tellus a ex eleifend mattis. In vitae ipsum in mauris vestibulum imperdiet.</p>
<div class="btn" style="left:582px;top:1784px;width:151px;height:52px;background:var(--green)">READ MORE</div>

<section class="seek" role="img" aria-label="Dim office scene of a job interview across a table"></section>
<h2 class="seek-title">SEEKING FOR A JOB?</h2>
<p class="seek-sub">BROWSE HUNDREDS OF JOB OFFERS AND FIND THE BEST SUITABLE POSITION</p>
<div class="btn" style="left:424px;top:2190px;width:172px;height:57px;background:var(--green)">SEARCH JOBS</div>
<div class="btn" style="left:603px;top:2190px;width:173px;height:57px;background:var(--red)">ADD A RESUME</div>

<h2 class="section-title" style="top:2490px">RECENT <span class="red">JOB</span></h2>
<p class="jobs-sub">Sed ut perspiciatis unde omnis iste natus error sit voluptatem accusantium doloremque laudantium</p>

<div class="jobs-table">
  <div class="job-row" style="top:0;height:80px">
    <div class="badge" style="top:11px"><i></i></div>
    <div class="role" style="top:26px">SED UT PERSPICIATIS<em>Company inc.</em></div>
    <div class="sep" style="left:313px"></div>
    <div class="loc" style="top:30px"><svg width="10" height="14" viewBox="0 0 10 14"><path d="M5 0a5 5 0 0 0-5 5c0 4 5 9 5 9s5-5 5-9a5 5 0 0 0-5-5zm0 7a2 2 0 1 1 0-4 2 2 0 0 1 0 4z" fill="#999"/></svg>New York City</div>
    <div class="sep" style="left:511px"></div>
    <div class="type" style="top:21px;background:var(--red)">FULL TIME</div>
    <div class="sep" style="left:738px"></div>
    <div class="price" style="top:27px">$ 55.00</div>
  </div>
  <div class="job-row" style="top:80px;height:92px">
    <div class="badge" style="top:17px"><i></i></div>
    <div class="role" style="top:33px">SED UT PERSPICIATIS<em>Company inc.</em></div>
    <div class="sep" style="left:313px"></div>
    <div class="loc" style="top:36px"><svg width="10" height="14" viewBox="0 0 10 14"><path d="M5 0a5 5 0 0 0-5 5c0 4 5 9 5 9s5-5 5-9a5 5 0 0 0-5-5zm0 7a2 2 0 1 1 0-4 2 2 0 0 1 0 4z" fill="#999"/></svg>New York City</div>
    <div class="sep" style="left:511px"></div>
    <div class="type" style="top:27px;background:var(--green-dark)">PART TIME</div>
    <div class="sep" style="left:738px"></div>
    <div class="price" style="top:33px">$ 35.00</div>
  </div>
  <div class="job-row" style="top:172px;height:91px">
    <div class="badge" style="top:16px"><i></i></div>
    <div class="role" style="top:32px">SED UT PERSPICIATIS<em>Company inc.</em></div>
    <div class="sep" style="left:313px"></div>
    <div class="loc" style="top:36px"><svg width="10" height="14" viewBox="0 0 10 14"><path d="M5 0a5 5 0 0 0-5 5c0 4 5 9 5 9s5-5 5-9a5 5 0 0 0-5-5zm0 7a2 2 0 1 1 0-4 2 2 0 0 1 0 4z" fill="#999"/></svg>New York City</div>
    <div class="sep" style="left:511px"></div>
    <div class="type" style="top:27px;background:var(--purple)">FREELANCE</div>
    <div class="sep" style="left:738px"></div>
    <div class="price" style="top:33px">$ 65.00</div>
  </div>
  <div class="job-row" style="top:263px;height:89px;border-bottom:0">
    <div class="badge" style="top:15px"><i></i></div>
    <div class="role" style="top:31px">SED UT PERSPICIATIS<em>Company inc.</em></div>
    <div class="sep" style="left:313px"></div>
    <div class="loc" style="top:35px"><svg width="10" height="14" viewBox="0 0 10 14"><path d="M5 0a5 5 0 0 0-5 5c0 4 5 9 5 9s5-5 5-9a5 5 0 0 0-5-5zm0 7a2 2 0 1 1 0-4 2 2 0 0 1 0 4z" fill="#999"/></svg>New York City</div>
    <div class="sep" style="left:511px"></div>
    <div class="type" style="top:26px;background:var(--green-dark)">PART TIME</div>
    <div class="sep" style="left:738px"></div>
    <div class="price" style="top:32px">$ 25.00</div>
  </div>
</div>

<svg class="abs" style="left:58px;top:3200px" width="28" height="100" viewBox="0 0 28 100"><path d="M26 2 2 50l24 48" fill="none" stroke="#aaa" stroke-width="1.5"/></svg>
<svg class="abs" style="left:1114px;top:3200px" width="28" height="100" viewBox="0 0 28 100"><path d="M2 2l24 48L2 98" fill="none" stroke="#aaa" stroke-width="1.5"/></svg>
<div class="portrait" role="img" aria-label="Portrait of a smiling businesswoman in glasses"></div>
<div class="quote-dot">”</div>
<h2 class="test-title">OUR <span class="red">TESTIMONIALS</span></h2>
<p class="test-copy">I was highly impressed by the professionalism shown during my interview process. It was less an interview and more of a conversation with the recruiter. I felt comfortable sharing my previous management experience and all of my qualifications for the Operations Manager position. I was informed about Harbor Dental Group® History, Mission and Values with pride and enthusias</p>
<div class="test-name">Maren Holt- <small>CEO in Company Name</small></div>

<footer class="footer"></footer>
<div class="foot-brand on-footer"><div class="name">PLORVEX</div><div class="tag">SERVICING YOU SINCE 1980</div></div>
<div class="foot-h on-footer" style="left:420px">LINKS</div>
<ul class="foot-links on-footer">
  <li><span>»</span>HOME</li><li><span>»</span>INDUSTRIES</li><li><span>»</span>JOBS</li><li><span>»</span>CONTACT US</li>
</ul>
<div class="foot-h on-footer" style="left:616px">CONTACT US</div>
<div class="foot-contact on-footer">Tele : +1 800 555 0142<br>Fax : +1 800 555 0143<br>hello@plorvex.com<br>18 Linden Row, Apt. 303<br>Ashford, NY 10016 USA</div>
<div class="foot-h on-footer" style="left:862px">NEWSLETTER</div>
<p class="news-copy on-footer">Sed ut perspiciatis unde error sit vol uptatem accusantium...</p>
<div class="news-input">Enter Email Id :</div>
<div class="news-btn">Submit</div>
<div class="copyright on-footer">© Copyright 2020 Plorvex.All Rights Reserved</div>
<div class="social" style="left:878px"></div>
<div class="social" style="left:921px"></div>
<div class="social" style="left:964px"></div>
<div class="social" style="left:1007px"></div>
<div class="social" style="left:1050px"></div>
<div class="foot-code on-footer">C2</div>

</body>
</html>
```